BRISKEL Need a luxury modern business card designed.

Need a luxury modern business card designed. refer to the uploaded files for the company name and logo in the zip file under source files. i will making my descion on monday. so please send in before then so if we need to edit we will have the time. we have a trade show coming up and im on a deadline for printer.

Target Market(s)

high end clients

Contact Information for Business Card

Company nAme and logo. Tobias Fennick Co-Founder / Project Manager Office # 555-318-7094 Cell # 555-642-1586 BRISKEL.CA Tobias@briskel-example.ca

Font styles to use
Other font styles liked:
• Modern

Requirements
Must have
• Company name and logo, contact info, using the black, gold and white color scheme.

```html
<!DOCTYPE html>
<html lang="en">
<head>
<meta charset="utf-8">
<title>BRISKEL Business Card</title>
<link rel="stylesheet" href="https://fonts.googleapis.com/css2?family=Work+Sans:wght@400;500;600&display=swap">
<style>
  :root {
    --backdrop: #161616;
    --backdrop-edge: #0b0b0b;
    --card: #1c1c1c;
    --card-sheen: #2a2a2a;
    --gold: #b8a772;
    --white: #f4f4f2;
    --silver: #8e8e8e;
    --rule: #6f6f6f;
  }
  * { margin: 0; padding: 0; box-sizing: border-box; }
  html, body {
    width: 1200px;
    height: 900px;
    overflow: hidden;
  }
  body {
    background: radial-gradient(ellipse at 55% 45%, var(--backdrop) 0%, var(--backdrop-edge) 100%);
    font-family: "Work Sans", Arial, sans-serif;
    display: flex;
    flex-direction: column;
    align-items: center;
    justify-content: center;
    gap: 34px;
  }
  .card {
    width: 700px;
    height: 400px;
    background: linear-gradient(135deg, var(--card) 0%, var(--card) 55%, var(--card-sheen) 100%);
    box-shadow: 0 14px 30px rgba(0,0,0,0.6);
    position: relative;
  }

  /* Front */
  .card-front {
    display: flex;
    align-items: center;
    justify-content: center;
  }
  .brand {
    display: flex;
    flex-direction: column;
    align-items: center;
  }
  .brand-row {
    display: flex;
    align-items: center;
    gap: 16px;
  }
  .brand-square {
    width: 18px;
    height: 18px;
    background: var(--silver);
  }
  .brand-name {
    font-weight: 400;
    font-size: 56px;
    letter-spacing: 10px;
    color: var(--silver);
    line-height: 1;
  }
  .brand-tagline {
    display: flex;
    align-items: center;
    gap: 10px;
    margin-top: 12px;
    font-size: 12px;
    letter-spacing: 5px;
    color: var(--silver);
  }
  .brand-tagline::before,
  .brand-tagline::after {
    content: "";
    width: 46px;
    height: 1px;
    background: var(--rule);
  }

  /* Back */
  .card-back {
    display: flex;
    align-items: center;
    padding: 0 56px 0 52px;
  }
  .card-back .brand { width: 250px; }
  .card-back .brand-name {
    font-size: 40px;
    letter-spacing: 7px;
    color: var(--white);
  }
  .card-back .brand-square {
    width: 14px;
    height: 14px;
    background: var(--gold);
  }
  .card-back .brand-tagline {
    font-size: 9px;
    letter-spacing: 4px;
    color: var(--white);
  }
  .card-back .brand-tagline::before,
  .card-back .brand-tagline::after { width: 30px; background: var(--white); }
  .divider {
    width: 2px;
    height: 150px;
    background: var(--gold);
    margin: 0 44px 0 38px;
  }
  .person-name {
    font-weight: 600;
    font-size: 34px;
    color: var(--gold);
    line-height: 1.1;
  }
  .person-title {
    font-size: 17px;
    color: var(--white);
    margin-bottom: 16px;
    letter-spacing: 0.5px;
  }
  .contact-list { list-style: none; }
  .contact-item {
    display: flex;
    align-items: center;
    gap: 10px;
    font-size: 17px;
    color: var(--white);
    letter-spacing: 0.6px;
    line-height: 1.55;
  }
  .contact-icon {
    width: 13px;
    height: 13px;
    flex: none;
  }
</style>
</head>
<body>

  <section class="card card-front">
    <div class="brand">
      <div class="brand-row">
        <span class="brand-square"></span>
        <span class="brand-name">BRISKEL</span>
      </div>
      <div class="brand-tagline">LUXURY LANDSCAPES</div>
    </div>
  </section>

  <section class="card card-back">
    <div class="brand">
      <div class="brand-row">
        <span class="brand-square"></span>
        <span class="brand-name">BRISKEL</span>
      </div>
      <div class="brand-tagline">LUXURY LANDSCAPES</div>
    </div>

    <div class="divider"></div>

    <div class="contact">
      <h1 class="person-name">Tobias Fennick</h1>
      <p class="person-title">Co-Founder</p>
      <ul class="contact-list">
        <li class="contact-item">
          <svg class="contact-icon" viewBox="0 0 16 16" aria-hidden="true">
            <path d="M4 1.5 L6 4.5 L4.6 6 C5.4 8 7.8 10.5 10 11.4 L11.5 10 L14.5 12 L13 14.5 C7 14 2 9 1.5 3 Z" fill="none" stroke="#b8a772" stroke-width="1.4"/>
          </svg>
          555-318-7094
        </li>
        <li class="contact-item">
          <svg class="contact-icon" viewBox="0 0 16 16" aria-hidden="true">
            <rect x="4" y="1" width="8" height="14" rx="1.5" fill="none" stroke="#b8a772" stroke-width="1.4"/>
            <line x1="7" y1="12.5" x2="9" y2="12.5" stroke="#b8a772" stroke-width="1.4"/>
          </svg>
          555-642-1586
        </li>
        <li class="contact-item">
          <svg class="contact-icon" viewBox="0 0 16 16" aria-hidden="true">
            <rect x="1" y="3" width="14" height="10" fill="none" stroke="#b8a772" stroke-width="1.4"/>
            <path d="M1 3 L8 9 L15 3" fill="none" stroke="#b8a772" stroke-width="1.4"/>
          </svg>
          briskel.ca Tobias@briskel-example.ca
        </li>
      </ul>
    </div>
  </section>

</body>
</html>
```